Professional Vehicle Wrap Design | 2020 Bexon Corvale | RV Tolk

We are seeking a full van wrap design for a 2020 Bexon Corvale K-300 Cargo Van that will represent RV Tolk. The primary color for this wrap should be sky blue to align with their branding and create a bold, professional appearance that stands out on the road.

Vehicle Details:

2020 Bexon Corvale K-300

Low Roof

129.9" Wheelbase (Regular)

Cargo configuration with sliding door on the right and dual rear doors (no side windows)

Design Requirements:

The wrap should feature sky blue as the dominant color.

Incorporate the RV Tolk logo and branding elements (logo files provided).

Design should be clean, professional, and highly visible for branding impact.

Avoid placing important text or graphics across sliding doors, seams, or complex panel curves to ensure durability and readability.

The design should complement the cargo van’s panel layout and utilize the full available wrap area effectively.

Included Files:
Download all project assets here: https://www.filevaultia.test/share/q8rk2mzn4tpw7vbd1xcl/KpZeRt73muLqwnYbHsAFcVe?key=x714nm3pqdzt2wbk9s6yr&v=htzp4qme&dl=0

We look forward to seeing creative and impactful wrap designs that help RV Tolk stand out.
*Final Files must be exported on the template provided
https://www.rvtolk.test/

Target Market(s)

RV Tolk serves homeowners, businesses, and property managers in Florence, AL. The wrap should convey professionalism and reliability to attract local clients seeking quality contracting and HVAC services.

Industry/Entity Type

RV Tolk operates in the HVAC and general contracting industry, providing heating, ventilation, and air conditioning services.

Colors

Designer to choose colors to be used in the design.

Requirements
Must have
• The wrap must feature sky blue as the primary color and prominently display the RV Tolk logo. The design should be bold, professional, and clean, avoiding critical text or graphics on sliding doors and seams. It should effectively use the full cargo van wrap area and ensure high visibility and easy brand recognition on the road.
Nice to have
• It would be great if the design incorporates subtle icons or visuals representing RV Tolk’s services, uses complementary colors to enhance the sky blue, and includes space for contact information without cluttering the overall look.
Should not have
• The design should not include overly busy patterns or small text that’s hard to read from a distance. Avoid placing important information over sliding door seams or complex curves, and steer clear of colors that clash with the primary sky blue.

```html
<!DOCTYPE html>
<html lang="en">
<head>
<meta charset="utf-8">
<title>RV Tolk Van Wrap</title>
<link rel="stylesheet" href="https://fonts.googleapis.com/css2?family=Roboto+Condensed:wght@700;800&display=swap">
<style>
  :root {
    --backdrop: #b9b9b9;
    --backdrop-light: #e6e6e6;
    --van-white: #f7f8f9;
    --trim-black: #1e1f21;
    --glass: #7b7f84;
    --sky: #2fa9e6;
    --sky-light: #6cc8f3;
    --navy: #1a3f99;
    --lamp: #c8262f;
    --tyre: #161616;
    --rim: #b7bcc2;
    --white: #ffffff;
  }
  html, body {
    margin: 0;
    width: 1200px;
    height: 1174px;
    overflow: hidden;
    background: radial-gradient(ellipse at 50% 50%, var(--backdrop-light) 0%, var(--backdrop) 80%);
    font-family: "Roboto Condensed", "Arial Narrow", sans-serif;
  }
  .wrap-sheet { display: block; width: 1200px; height: 1174px; }
  .brand-name { font-weight: 800; font-size: 78px; fill: var(--navy); letter-spacing: 1px; }
  .brand-line { font-weight: 700; font-size: 22px; fill: var(--navy); }
  .banner-text { font-weight: 800; font-size: 29px; fill: var(--white); font-style: italic; }
</style>
</head>
<body>
<svg class="wrap-sheet" viewBox="0 0 1200 1174" xmlns="http://www.w3.org/2000/svg">
  <defs>
    <g id="van-side">
      <ellipse cx="600" cy="565" rx="540" ry="12" fill="#8f8f8f" opacity=".45"/>
      <path class="van-body" fill="var(--van-white)"
        d="M62 160 Q66 148 90 148 L790 147 Q820 148 850 180 L1000 290 Q1050 310 1110 330 Q1135 345 1135 380 L1140 420 L55 420 L52 200 Z"/>
      <path class="wrap-sky" fill="var(--sky)"
        d="M64 160 Q66 150 90 150 L318 150 Q330 230 390 300 Q470 380 535 412 L56 412 L54 200 Z"/>
      <rect role="img" aria-label="Snowflake decorations for cooling service" x="70" y="152" width="150" height="110" rx="20" fill="var(--sky-light)" opacity=".45"/>
      <rect role="img" aria-label="Flame decorations for heating service" x="90" y="255" width="120" height="150" rx="40" fill="var(--sky-light)" opacity=".45"/>
      <path fill="var(--glass)" d="M735 180 L810 178 Q830 182 845 200 L920 295 L920 318 L750 300 Q735 298 733 285 Z"/>
      <rect x="880" y="245" width="26" height="75" rx="6" fill="var(--trim-black)"/>
      <line x1="385" y1="150" x2="385" y2="420" stroke="#d3d6da" stroke-width="2"/>
      <line x1="700" y1="150" x2="700" y2="420" stroke="#d3d6da" stroke-width="2"/>
      <rect x="715" y="320" width="50" height="8" rx="4" fill="var(--trim-black)"/>
      <path fill="#444" d="M1040 312 L1110 345 L1118 372 L1080 370 Q1050 350 1040 330 Z"/>
      <rect x="62" y="282" width="26" height="128" rx="6" fill="var(--lamp)"/>
      <rect x="66" y="330" width="18" height="40" fill="var(--white)" opacity=".8"/>
      <path fill="var(--trim-black)" d="M50 412 L1145 412 L1152 425 L1152 490 Q1150 510 1120 510 L52 500 Z"/>
      <path fill="var(--sky)" d="M375 465 L850 465 L850 492 L382 492 Z"/>
      <path fill="var(--navy)" d="M640 465 L850 465 L850 492 L700 492 Q690 470 640 465 Z"/>
      <g class="wheel">
        <circle cx="280" cy="510" r="78" fill="var(--trim-black)"/>
        <circle cx="280" cy="510" r="72" fill="var(--tyre)"/>
        <circle cx="280" cy="510" r="46" fill="var(--rim)"/>
        <circle cx="280" cy="510" r="22" fill="#333"/>
      </g>
      <g class="wheel">
        <circle cx="970" cy="510" r="78" fill="var(--trim-black)"/>
        <circle cx="970" cy="510" r="72" fill="var(--tyre)"/>
        <circle cx="970" cy="510" r="46" fill="var(--rim)"/>
        <circle cx="970" cy="510" r="22" fill="#333"/>
      </g>
    </g>
  </defs>

  <g class="van van-left">
    <use href="#van-side"/>
    <path class="contact-banner" fill="var(--navy)" d="M92 345 L650 345 L625 365 L650 385 L92 385 Z"/>
    <line x1="376" y1="352" x2="376" y2="378" stroke="var(--sky)" stroke-width="4"/>
    <text class="banner-text" x="125" y="376">WWW.RVTOLK.TEST</text>
    <text class="banner-text" x="395" y="376">(256) 555 0148</text>
    <g class="brand-block">
      <text class="brand-line" x="395" y="212" text-anchor="middle">Heating &amp; Air</text>
      <text class="brand-name" x="395" y="285" text-anchor="middle">RV Tolk</text>
      <text class="brand-line" x="395" y="318" text-anchor="middle">&amp; Sons, Inc.</text>
    </g>
  </g>

  <g class="van van-right">
    <use href="#van-side" transform="translate(1200,472) scale(-1,1)"/>
    <path class="contact-banner" fill="var(--navy)" d="M550 817 L1108 817 L1108 857 L550 857 L575 837 Z"/>
    <line x1="824" y1="824" x2="824" y2="850" stroke="var(--sky)" stroke-width="4"/>
    <text class="banner-text" x="595" y="848">(256) 555 0148</text>
    <text class="banner-text" x="840" y="848">WWW.RVTOLK.TEST</text>
    <g class="brand-block">
      <text class="brand-line" x="805" y="684" text-anchor="middle">Heating &amp; Air</text>
      <text class="brand-name" x="805" y="757" text-anchor="middle">RV Tolk</text>
      <text class="brand-line" x="805" y="790" text-anchor="middle">&amp; Sons, Inc.</text>
    </g>
  </g>
</svg>
</body>
</html>
```